IT solutions & services company requires stationary makeover

Looking for a consistent modern, professional design across our printed client touch points:
Business Cards
Letterhead
Client proposal
Flyer
Postcard

We provide solutions for SME IT - servers, backups, AV etc, and the ongoing services around them.
we are happy with our logo - please see attached and would like the colour theme to be maintained.

```html
<!DOCTYPE html>
<html lang="en">
<head>
<meta charset="utf-8">
<title>Tessrow IT — Stationery Set</title>
<link href="https://fonts.googleapis.com/css2?family=Montserrat:wght@400;600;700&family=Open+Sans:wght@400;600&display=swap" rel="stylesheet">
<style>
  :root{
    --brand-blue:#1389bf;
    --brand-blue-deep:#0b7fb2;
    --ink:#121212;
    --paper:#ffffff;
    --stage:#e8e9eb;
    --muted:#6b6f74;
  }
  *{box-sizing:border-box;margin:0;padding:0}
  html,body{width:1200px;height:795px;overflow:hidden;background:var(--stage)}
  body{position:relative;font-family:"Open Sans",Arial,sans-serif;color:var(--ink)}

  .sheet{position:absolute;background:var(--paper);overflow:hidden;box-shadow:0 2px 8px rgba(0,0,0,.12)}
  .sheet svg.art{position:absolute;inset:0;width:100%;height:100%}

  .brand{font-family:"Montserrat",Arial,sans-serif;font-weight:700;color:var(--ink);display:flex;align-items:center;gap:6px;white-space:nowrap;position:absolute}
  .brand-dot{width:10px;height:10px;border-radius:50%;background:var(--brand-blue)}

  .contact-list{list-style:none;font-size:6.5px;line-height:1.7;color:var(--ink)}
  .contact-list li::before{content:"";display:inline-block;width:4px;height:4px;background:var(--brand-blue);margin-right:4px;vertical-align:middle}

  /* Letterhead */
  .letterhead{left:60px;top:50px;width:300px;height:424px}
  .letterhead .brand{right:24px;top:26px;font-size:16px}
  .letterhead .signoff{position:absolute;right:20px;bottom:8px;display:flex;gap:8px;align-items:flex-start}
  .signoff .person{text-align:right;border-right:1px solid var(--brand-blue);padding-right:8px}
  .person-name{font-family:"Montserrat",Arial,sans-serif;font-size:9px;font-weight:600;color:var(--brand-blue)}
  .person-role{font-size:5.5px;color:var(--muted);text-transform:uppercase;letter-spacing:.4px}
  .letterhead .contact-list{font-size:6px;line-height:1.55}

  /* Proposal cover */
  .cover{left:450px;top:50px;width:300px;height:424px}
  .cover-band{position:absolute;left:0;top:0;width:100%;height:300px;background:var(--brand-blue-deep)}
  .cover-title{position:absolute;left:26px;top:150px;color:#fff}
  .cover-title h1{font-family:"Montserrat",Arial,sans-serif;font-weight:600;font-size:20px}
  .cover-title p{font-size:7px;opacity:.85;margin-top:3px}
  .cover-date{position:absolute;left:26px;top:210px;font-family:"Montserrat",Arial,sans-serif;font-size:12px;color:#fff;letter-spacing:1px}
  .cover-foot{position:absolute;left:24px;right:24px;bottom:34px;display:flex;justify-content:space-between;align-items:center}
  .cover-foot .brand{position:static;font-size:15px}
  .cover-foot .contact-list{border-left:1px solid var(--brand-blue);padding-left:8px}

  /* Sample page */
  .sample{left:840px;top:50px;width:300px;height:424px}
  .sample .brand.top{left:24px;top:26px;font-size:12px}
  .sample-head{position:absolute;right:24px;top:58px;text-align:right}
  .sample-head h2{font-family:"Montserrat",Arial,sans-serif;font-size:15px;font-weight:700;color:var(--brand-blue)}
  .sample-head p{font-size:6px;color:var(--muted)}
  .sample-body{position:absolute;left:24px;right:24px;top:102px;font-size:6.5px;line-height:1.55}
  .sample-body p{margin-bottom:8px}
  .sample .brand.foot{right:24px;bottom:48px;font-size:12px}
  .sample-rule{position:absolute;left:24px;right:24px;bottom:36px;height:1px;background:var(--brand-blue)}
  .sample-contacts{position:absolute;left:24px;right:24px;bottom:22px;display:flex;justify-content:space-between;list-style:none;font-size:5.5px}
  .sample-contacts li::before{content:"";display:inline-block;width:4px;height:4px;background:var(--brand-blue);margin-right:3px;vertical-align:middle}

  /* Business cards */
  .card{top:560px;width:230px;height:130px}
  .card-1{left:80px}
  .card-2{left:350px;background:var(--ink)}
  .card-3{left:620px}
  .card-4{left:890px}
  .card .brand{right:20px;top:40px;font-size:17px}
  .card-back .brand{position:absolute;left:18px;top:50px;font-size:10px;color:#fff}
  .card-back .details{position:absolute;right:16px;top:20px;text-align:right}
  .card-back .person-name{font-size:12px}
  .card-back .person-role{color:#cfd2d6}
  .card-back .contact-list{color:#fff;margin-top:8px;font-size:6px}
</style>
</head>
<body>

<section class="sheet letterhead" aria-label="Letterhead">
  <svg class="art" viewBox="0 0 300 424" preserveAspectRatio="none" aria-hidden="true">
    <path d="M0 40 C30 200 150 305 300 345 L300 366 C140 340 20 250 0 150 Z" fill="var(--brand-blue)"/>
    <path d="M110 300 C165 340 230 362 300 370 L300 381 C215 378 155 350 110 300 Z" fill="var(--ink)"/>
  </svg>
  <div class="brand"><span class="brand-dot"></span>Tessrow IT</div>
  <div class="signoff">
    <div class="person">
      <div class="person-name">Aaron Pell</div>
      <div class="person-role">Managing Director</div>
    </div>
    <ul class="contact-list">
      <li>+1 555 014 2290</li>
      <li>hello@tessrowit.com</li>
      <li>12 Harbour Lane, Leeds</li>
    </ul>
  </div>
</section>

<section class="sheet cover" aria-label="Client proposal cover">
  <div class="cover-band"></div>
  <div class="cover-title">
    <h1>Company Overview</h1>
    <p>An introduction to our services and support</p>
  </div>
  <div class="cover-date">August 2014</div>
  <div class="cover-foot">
    <div class="brand"><span class="brand-dot"></span>Tessrow IT</div>
    <ul class="contact-list">
      <li>+1 555 014 2290</li>
      <li>hello@tessrowit.com</li>
      <li>12 Harbour Lane, Leeds</li>
    </ul>
  </div>
</section>

<section class="sheet sample" aria-label="Proposal text page">
  <div class="brand top"><span class="brand-dot"></span>Tessrow IT</div>
  <div class="sample-head">
    <h2>Sample Text</h2>
    <p>A short summary of the services we provide</p>
  </div>
  <div class="sample-body">
    <p>Our team designs, installs and supports server, backup and audio visual systems for growing businesses, keeping every office running smoothly from the first day onward.</p>
    <p>We review current hardware, plan sensible upgrades and manage the whole rollout so staff can keep working without long interruptions or lost files.</p>
    <p>Each client gets a named engineer, clear monthly reports and a support line that answers quickly, whether the issue is a failed drive or a new meeting room screen.</p>
    <p>Backups are checked every week and restored on a test schedule, so recovery is proven before it is ever needed.</p>
  </div>
  <div class="brand foot"><span class="brand-dot"></span>Tessrow IT</div>
  <div class="sample-rule"></div>
  <ul class="sample-contacts">
    <li>+1 555 014 2290</li>
    <li>www.tessrowit.com</li>
    <li>12 Harbour Lane, Leeds</li>
  </ul>
</section>

<section class="sheet card card-1" aria-label="Business card front">
  <svg class="art" viewBox="0 0 230 130" preserveAspectRatio="none" aria-hidden="true">
    <path d="M0 60 L0 130 L90 130 C50 115 20 95 0 60 Z" fill="var(--brand-blue)"/>
    <path d="M40 108 C80 122 130 122 170 112 C130 128 80 130 40 108 Z" fill="var(--ink)"/>
  </svg>
  <div class="brand"><span class="brand-dot"></span>Tessrow IT</div>
</section>

<section class="sheet card card-2 card-back" aria-label="Business card back">
  <div class="brand"><span class="brand-dot"></span>Tessrow IT</div>
  <div class="details">
    <div class="person-name">Aaron Pell</div>
    <div class="person-role">Managing Director</div>
    <ul class="contact-list">
      <li>+1 555 014 2290</li>
      <li>hello@tessrowit.com</li>
      <li>www.tessrowit.com</li>
      <li>12 Harbour Lane, Leeds</li>
    </ul>
  </div>
</section>

<section class="sheet card card-3" aria-label="Business card front">
  <svg class="art" viewBox="0 0 230 130" preserveAspectRatio="none" aria-hidden="true">
    <path d="M0 40 L0 130 L120 130 C60 115 20 85 0 40 Z" fill="var(--brand-blue)"/>
    <path d="M30 70 C70 110 130 118 190 108 C130 126 70 118 30 70 Z" fill="var(--ink)"/>
  </svg>
  <div class="brand"><span class="brand-dot"></span>Tessrow IT</div>
</section>

<section class="sheet card card-4" aria-label="Business card front">
  <svg class="art" viewBox="0 0 230 130" preserveAspectRatio="none" aria-hidden="true">
    <path d="M0 40 L0 130 L120 130 C60 115 20 85 0 40 Z" fill="var(--brand-blue)"/>
    <path d="M30 70 C70 110 130 118 190 108 C130 126 70 118 30 70 Z" fill="var(--ink)"/>
  </svg>
  <div class="brand"><span class="brand-dot"></span>Tessrow IT</div>
</section>

</body>
</html>
```